Website development company website

ABOUT COMPANY
Hi everyone! We're a Melbourne, Australia website development company in a need of a website design that will make online store merchants want to engage our services.
We specialise exclusively in Torvista e-commerce platform (https://torvista-platform.example/). What distinguishes our business from competition is that rather than designing and building brand new websites, we offer development, support and maintenance services to established websites. Maintenance and Support are the keywords representing our business.
Our potential clients are people with broken, slow and underperforming Torvista installations who need assistance getting their websites up and making sales. Our website must pass the message that we can help, and provide quick means of making contact.
DESIGN
Overall, we're looking for a slick, clean, airy, conservative design. No need to do anything crazy, try to stick to what's "standard" in website design these days and make it easy on all of us. The website is unlikely to be updated too often so it needs to look attractive and fresh first time over and after a year, too.
Attached is our new logo, which you'll be able to take the basic idea from, the colors and fonts. Though, don't use the fonts from the logo in the website, stick to the standard widely supported fonts. Additional use of Google fonts is fine.
Don't overdo it with colors, stick to conservative basic color set and only use the colors from the log for accents like headings etc. Please, don't be tempted to use the blue and orange as background of whole blocks, other than perhaps footer. Thanks.
For the images used, I'd like to stay away from a design studio/digital agency feel and lean more towards professional support and maintenance services. I'm thinking images of content merchants doing their job. Something along the lines of "We'll be taking care of the website so that you only need to care about the business".
Some ideas I like:
http://www.plumframe-pics.example/detail/photo/portrait-of-confident-male-design-professional-royalty-free-image/572048163
http://www.plumframe-pics.example/detail/photo/designer-taking-picture-of-hat-high-res-stock-photography/839207514
http://www.plumframe-pics.example/detail/photo/woman-packaging-pottery-royalty-free-image/216684093
Images of colorful shopping bags and shopping carts are over the top and not serious enough. Instead of images matching Online Shopping, I'd try going more for Stability, Reliability, Performance.
Our existing website is http://www.bravuln.example. Please, don't take design ideas from it, but it will give you a picture of the structure of our new website and content that's going to be used initially.
If you could include a basic icon set to use throughout the website, that would be great. If the icons could match our logo (attached), it would be a big plus.
ALL PAGES
Every page must contain clearly visible phone number (1300 648 907) and a Contact Us Now button, which opens an AJAX driven popup form with Name, Email, Phone and Message to be sent through.
To start with, main menu items will be Torvista, Portfolio, Contact.
At the bottom of each page, please, include a newsletter subscription form with text Subscribe to Torvista Support and Security Updates.
For the footer, I'd like to see a logo strip with the following logos in grayscale (no need to link anywhere): Torvista, QRX, DataVane, NCB. You'll find the logos on Google Images.
Standard footer columns follow. Here, I'd like to see logos in color: Torvista Certified Developer, Torvista Ceritified Solution Provider. Again, the logos are on Google Images.
No social media logos/links necessary anywhere on the website.
...and then the copyright line.
FRONT PAGE
Large slider with images that would appeal to our target audience. Keywords here would be Torvista System Audit, Torvista Performance Optimisation, Torvista Website Emergency Recovery, Torvista Development Infrastructure Hosting. We'll have a static page created for each of these to link to.
In a corner of the slider, or on the edge, can I have an overlay with logos in color (same as footer): Torvista Certified Developer, Torvista Ceritified Solution Provider.
Underneath, a number of blocks, each with an image and teaser that we'll use to link to various pages throughout the website.
PORTFOLIO PAGE
I'm thinking a single long page with a block per client, which will contain project name, description from us and a testimonial from client. Also, each block will contain a single large screenshot. No gallery or slideshow is necessary here, just one image per project.
I'll leave the layout up to you, but try to put yourself in the shoes of a potential client reviewing our past work by simply scrolling down this one page.
CONTACT US PAGE
Separate page with the same form as above, phone number (1300 648 907), email address (support@kavreo.example), address (Suite 42, Level 3|8 Wattlebrook Lane|Fernvale Heights VIC 3999), and a grayscale Google Map.
CODING UP
Coding up into static HTML/CSS/JS is equally important as the design itself. We're a website development company, we'll be integrating the theme. We will spot any issues and we will point them out.
Coded up design must be fully responsive. Enough said.
To be able to create any content in future, we'd like one extra page coded up with samples of all themed elements, lists, forms, buttons, 2, 3, 4-column layout, alerts, icons, etc. This page does not need to be designed, only coded up.
The design will be integrated into Drupal using Twig. If possible at all, try to keep it in mind when designing and coding up, and make the integration into a Drupal theme easier for us.
GOOD LUCK!
That's it. Let me know if anything needs clarifying. So far I've had a great experience with ArtFlockly. I don't doubt some great designs will emerge. Clever ideas are highly appreciated, but also make it clear you've read and followed the points in this brief. Cheers, Tom

```html
<!DOCTYPE html>
<html lang="en">
<head>
<meta charset="utf-8">
<title>Contact Us – Kestrova E-Commerce</title>
<link href="https://fonts.googleapis.com/css2?family=Roboto:wght@400;500;700&family=Roboto+Condensed:wght@700&family=Ubuntu:wght@400;500&display=swap" rel="stylesheet">
<style>
:root{
  --orange:#e5802b;
  --navy:#0e3c6e;
  --navy-deep:#0b325c;
  --ink:#333;
  --muted:#555;
  --strip:#f6f6f6;
  --line:#e2e2e2;
  --logo-grey:#a9a9a9;
}
*{box-sizing:border-box;margin:0;padding:0}
html,body{width:824px;height:1200px;overflow:hidden}
body{position:relative;font-family:"Ubuntu",sans-serif;color:var(--ink);background:#fff}
.abs{position:absolute}
.top-bar{left:0;top:0;width:824px;height:23px;background:var(--orange);font:400 8.5px "Roboto",sans-serif;color:#fff}
.top-bar .item{position:absolute;top:6px;display:flex;align-items:center;gap:5px}
.top-bar .sep{position:absolute;top:0;width:1px;height:23px;background:rgba(255,255,255,.35)}
.site-header{left:0;top:23px;width:824px;height:68px;background:#fff}
.brand{position:absolute;left:68px;top:20px;display:flex;align-items:center;gap:8px;font:500 22px "Roboto",sans-serif;color:var(--navy)}
.brand .mark{width:24px;height:24px;background:var(--orange)}
.main-nav{position:absolute;top:30px;font:400 11px "Roboto",sans-serif;color:#222}
.main-nav a{position:absolute;white-space:nowrap;color:inherit;text-decoration:none}
.main-nav a.active{color:var(--orange)}
.hero{left:0;top:91px;width:824px;height:110px;background:linear-gradient(100deg,#4d6f95 0%,#6f8fb2 35%,#55789f 65%,#1f3f66 100%)}
.hero h1{position:absolute;left:0;top:28px;width:100%;text-align:center;font:700 27px "Roboto Condensed",sans-serif;color:#fff}
.hero p{position:absolute;left:0;top:63px;width:100%;text-align:center;font:400 14.5px "Roboto",sans-serif;color:#fff}
.contact-info{font-size:9.5px;line-height:16.5px;color:var(--muted)}
.icon-circle{width:22px;height:22px;border-radius:50%;background:#111;display:flex;align-items:center;justify-content:center}
.map{left:68px;top:309px;width:688px;height:245px;background:linear-gradient(135deg,#e4e4e4,#d6d6d6 60%,#e0e0e0)}
.message-box{left:185px;top:584px;width:514px;height:135px;border:1px solid var(--line);box-shadow:inset 0 2px 3px rgba(0,0,0,.05)}
.message-box span{position:absolute;left:16px;top:9px;font-size:8px;color:#444}
.submit{left:345px;top:748px;width:134px;height:30px;background:var(--navy);color:#fff;font:400 13px "Roboto",sans-serif;display:flex;align-items:center;justify-content:center;border-radius:2px}
.tech-strip{left:0;top:815px;width:824px;height:68px;background:var(--strip);border-top:1px solid #eee}
.tech-strip span{position:absolute;top:26px;font:500 12px "Roboto",sans-serif;color:var(--logo-grey);width:90px;text-align:center}
.subscribe{left:0;top:883px;width:824px;height:87px;background:var(--orange)}
.subscribe .label{position:absolute;left:170px;top:29px;font:400 11px/16px "Roboto",sans-serif;color:#fff}
.subscribe .field{position:absolute;left:387px;top:30px;width:256px;height:29px;background:#fff;border-radius:15px 0 0 15px;font-size:8.5px;color:#555;padding:10px 17px}
.subscribe .btn{position:absolute;left:643px;top:30px;width:86px;height:29px;background:#333;border-radius:0 15px 15px 0;color:#fff;font:400 9px "Roboto",sans-serif;display:flex;align-items:center;justify-content:center}
.site-footer{left:0;top:970px;width:824px;height:178px;background:var(--navy);color:#fff}
.footer-brand{position:absolute;left:68px;top:28px;display:flex;align-items:center;gap:8px;font:500 22px "Ubuntu",sans-serif}
.footer-brand .mark{width:24px;height:24px;background:#fff}
.footer-about{position:absolute;left:68px;top:82px;width:210px;font-size:8.5px;line-height:14px}
.read-more{position:absolute;left:68px;top:147px;font-size:8.5px}
.footer-map{position:absolute;left:288px;top:26px;width:268px;height:128px;background:linear-gradient(135deg,#e6e6e6,#cfcfcf)}
.footer-address h3{position:absolute;left:592px;top:24px;font:400 12.5px "Roboto",sans-serif;white-space:nowrap}
.footer-address li{position:absolute;left:592px;list-style:none;font-size:9.3px;line-height:17px;display:flex;gap:6px;white-space:nowrap}
.footer-address li svg{margin-top:4px;flex:none}
.copyright{left:0;top:1148px;width:824px;height:52px;background:var(--navy-deep);color:#fff;font-size:8.5px;text-align:center;padding-top:18px}
</style>
</head>
<body>

<div class="abs top-bar">
  <div class="item" style="left:436px"><svg width="8" height="8" viewBox="0 0 10 10"><path d="M2 0.5l2 2-1 1.2c.6 1.3 1.5 2.2 2.8 2.8l1.2-1 2 2-1.3 1.5C4.5 9 1 5.5.5 1.8z" fill="#fff"/></svg>Call Us + 1300 274 618</div>
  <div class="sep" style="left:556px"></div>
  <div class="item" style="left:572px"><svg width="9" height="7" viewBox="0 0 9 7"><rect x=".5" y=".5" width="8" height="6" fill="none" stroke="#fff"/><path d="M.5.5l4 3.2 4-3.2" fill="none" stroke="#fff"/></svg>info@bravuln.example</div>
  <div class="sep" style="left:681px"></div>
  <div class="item" style="left:698px"><svg width="7" height="8" viewBox="0 0 7 8"><circle cx="3.5" cy="2" r="2" fill="#fff"/><path d="M0 8c0-3 1.5-4 3.5-4S7 5 7 8z" fill="#fff"/></svg>Contact Me</div>
</div>

<header class="abs site-header">
  <div class="brand"><span class="mark"></span>Kestrova</div>
  <nav class="main-nav">
    <a class="active" style="left:490px">HOME</a>
    <a style="left:543px">ABOUT US</a>
    <a style="left:614px">PORTFOLIO</a>
    <a style="left:692px">CONTACT US</a>
  </nav>
</header>

<section class="abs hero" role="img" aria-label="Blurred photo of a person working at a desk, in blue tones">
  <h1>GET IN TOUCH</h1>
  <p>Please complete the form below, or call us on 1300 274 618</p>
</section>

<div class="abs icon-circle" style="left:215px;top:238px"><svg width="9" height="11" viewBox="0 0 9 11"><path d="M4.5 0A4.2 4.2 0 0 0 .3 4.2C.3 7.3 4.5 11 4.5 11s4.2-3.7 4.2-6.8A4.2 4.2 0 0 0 4.5 0z" fill="#fff"/><circle cx="4.5" cy="4.2" r="1.6" fill="#111"/></svg></div>
<div class="abs contact-info" style="left:247px;top:234px">Suite 42, Level 3|8 Wattlebrook Lane|<br>Fernvale Heights VIC 3999</div>
<div class="abs icon-circle" style="left:433px;top:238px"><svg width="10" height="10" viewBox="0 0 10 10"><path d="M2 0.5l2 2-1 1.2c.6 1.3 1.5 2.2 2.8 2.8l1.2-1 2 2-1.3 1.5C4.5 9 1 5.5.5 1.8z" fill="#fff"/></svg></div>
<div class="abs contact-info" style="left:466px;top:235px;font-size:10px;line-height:18px">Phone : (+1) 300 517 204<br>E - Mail : support@kavreo.example</div>

<div class="abs map" role="img" aria-label="Greyscale street map around the office location"></div>

<div class="abs message-box"><span>Message :</span></div>
<div class="abs submit">SUBMIT NOW</div>

<div class="abs tech-strip">
  <span style="left:44px">Torvista</span>
  <span style="left:120px">QRX</span>
  <span style="left:201px">DataVane</span>
  <span style="left:289px">NCB</span>
  <span style="left:387px">Stratovel</span>
  <span style="left:507px">Kelpwright</span>
  <span style="left:604px">Uptrellis</span>
  <span style="left:690px">Orvane</span>
</div>

<section class="abs subscribe">
  <svg class="abs" style="left:50px;top:14px" width="72" height="60" viewBox="0 0 72 60"><g transform="rotate(-28 36 30)" fill="none" stroke="#fff" stroke-opacity=".18" stroke-width="2"><rect x="10" y="14" width="52" height="34"/><path d="M10 14l26 20 26-20"/></g></svg>
  <svg class="abs" style="left:132px;top:29px" width="28" height="28" viewBox="0 0 28 28"><path d="M26 2L2 12l9 3 2 10 4-6 6 4z M11 15L26 2 13 25" fill="none" stroke="#fff" stroke-width="1.8" stroke-linejoin="round"/></svg>
  <div class="label">SUBSCRIBE TO TORVISTA SUPPORT AND<br>SECURITY UPDATES</div>
  <div class="field">Enter your E - mail</div>
  <div class="btn">SUBSCRIBE</div>
</section>

<footer class="abs site-footer">
  <div class="footer-brand"><span class="mark"></span>Kestrova</div>
  <p class="footer-about">Sed ut perspiciatis unde omnis iste natus error sit voluptatem accusantium doloremque laudantium, totam rem aperiam, eaque ipsa quae ab illo inven tore veritatis et quasi architecto beatae</p>
  <div class="read-more">Read More</div>
  <div class="footer-map" role="img" aria-label="Small greyscale map with an orange location pin"></div>
  <div class="footer-address">
    <h3>COMPANY ADDRESS</h3>
    <ul>
      <li style="top:56px"><svg width="7" height="9" viewBox="0 0 9 11"><path d="M4.5 0A4.2 4.2 0 0 0 .3 4.2C.3 7.3 4.5 11 4.5 11s4.2-3.7 4.2-6.8A4.2 4.2 0 0 0 4.5 0z" fill="#e5802b"/></svg><span>Suite 42, Level 3|8 Wattlebrook Lane|<br>Fernvale Heights VIC 3999</span></li>
      <li style="top:90px"><svg width="8" height="8" viewBox="0 0 10 10"><path d="M2 0.5l2 2-1 1.2c.6 1.3 1.5 2.2 2.8 2.8l1.2-1 2 2-1.3 1.5C4.5 9 1 5.5.5 1.8z" fill="#e5802b"/></svg><span>Phone:&nbsp; (1300 648 907)</span></li>
      <li style="top:107px"><svg width="8" height="7" viewBox="0 0 9 7"><rect width="9" height="7" fill="#e5802b"/><path d="M0 0l4.5 3.5L9 0" fill="none" stroke="#0e3c6e"/></svg><span>Email: support@kavreo.example</span></li>
    </ul>
  </div>
</footer>

<div class="abs copyright">© 2016 All copyrights Reserved. Kestrova E-Commerce</div>

</body>
</html>
```